Brackenford Fluidworks needs a website describing the repair business we are in.

Brackenford Fluidworks is a full hydraulic repair facility. We have 2 shops. We repair and service all hydraulic cylinders, pneumatic cylinders, hydraulic pumps, motors, valves and gearboxes. Our services range from large industrial plants to the individual that owns one piece of equipment. We also offer removal and install of cylinders. Along with free pick up and delivery, within a certain distance which is usually 100 miles from one of our shops.

With over 30 years experience in the hydraulic business, we can repair or replace any job. There is not a job too big or too small, we service them all.

We have customers that send whole pieces of equipment to us to do complete overhauls on all the hydraulics. Ranging from a country club green roller to a 10 ton boom truck.

Target Market(s)

Industrial plants, road builders, dirt work companies, general contractors, owners of industrial equipment (bulldozers, excavators, loaders, scrapers, motor graders, etc.

Industry/Entity Type

Hydraulic

Number of Pages Required

5+ page

Font styles to use
Sans Serif

Colors
ec1f27
ffffff
aaaaaa

Requirements
Must have
• Information about what we offer and pictures of jobs completed.
Nice to have
• Nice stock photos of jobsites and industrial plants.
Should not have
• Any sort of comical characters.

```html
<!DOCTYPE html>
<html lang="en">
<head>
<meta charset="utf-8">
<title>Brackenford Fluidworks – Hydraulic Repair</title>
<link rel="stylesheet" href="https://fonts.googleapis.com/css2?family=Lato:wght@400;700&family=Open+Sans:wght@400;600&display=swap">
<style>
  :root {
    --red: #ec1f27;
    --red-deep: #c8141b;
    --white: #ffffff;
    --grey: #aaaaaa;
    --grey-mid: #9a9a9a;
    --grey-dark: #666666;
    --grey-btn: #8c8c8c;
    --ink: #333333;
    --ink-soft: #555555;
    --panel: #dcdcdc;
  }
  * { margin: 0; padding: 0; box-sizing: border-box; }
  html, body { width: 1200px; height: 2687px; overflow: hidden; }
  body { position: relative; background: var(--white); font-family: "Open Sans", Arial, sans-serif; color: var(--ink); }
  .abs { position: absolute; }
  .heading { font-family: "Lato", Arial, sans-serif; font-weight: 700; text-transform: uppercase; }

  /* Header */
  .site-header { position: absolute; left: 0; top: 0; width: 1200px; height: 124px; background: var(--white); }
  .brand { position: absolute; left: 116px; top: 34px; display: flex; align-items: center; gap: 14px; }
  .brand-dot { width: 50px; height: 50px; border-radius: 50%; background: var(--red); }
  .brand-name { font-family: "Lato", Arial, sans-serif; font-weight: 700; color: var(--red); font-size: 19px; line-height: 22px; letter-spacing: 0.5px; text-transform: uppercase; }
  .pickup-note { position: absolute; right: 134px; top: 30px; display: flex; align-items: center; gap: 7px; font-family: "Lato", Arial, sans-serif; font-weight: 700; font-size: 14px; color: var(--red); text-transform: uppercase; }
  .main-nav { position: absolute; left: 473px; top: 72px; display: flex; gap: 38px; font-family: "Lato", Arial, sans-serif; font-weight: 700; font-size: 16px; color: var(--ink); text-transform: uppercase; }
  .main-nav .active { color: var(--red); }

  /* Hero */
  .hero { position: absolute; left: 0; top: 124px; width: 1200px; height: 530px; background: linear-gradient(160deg, #5d5d5a 0%, #3d3c3a 45%, #2a2928 100%); }
  .hero-title { position: absolute; left: 0; top: 168px; width: 1200px; text-align: center; color: var(--white); font-size: 44px; line-height: 48px; }
  .btn-outline { position: absolute; left: 526px; top: 290px; width: 150px; height: 44px; border: 2px solid var(--white); border-radius: 22px; color: var(--white); font-family: "Lato", Arial, sans-serif; font-size: 14px; text-transform: uppercase; display: flex; align-items: center; justify-content: center; }
  .slider-dots { position: absolute; left: 551px; top: 474px; display: flex; gap: 9px; }
  .slider-dots span { width: 14px; height: 14px; border-radius: 50%; background: var(--white); border: 2px solid var(--white); }
  .slider-dots span.current { background: transparent; }

  /* About */
  .about { position: absolute; left: 0; top: 654px; width: 1200px; height: 367px; background: linear-gradient(100deg, #d7121b 0%, #e41a23 50%, #c9121a 100%); text-align: center; color: var(--white); }
  .about h2 { position: absolute; left: 0; top: 64px; width: 1200px; font-size: 30px; }
  .about p { position: absolute; left: 232px; top: 120px; width: 736px; font-size: 16.5px; line-height: 26.5px; }
  .btn-pill { position: absolute; border-radius: 22px; color: var(--white); font-family: "Lato", Arial, sans-serif; font-size: 14px; text-transform: uppercase; display: flex; align-items: center; justify-content: center; }
  .about .btn-pill { left: 521px; top: 270px; width: 158px; height: 44px; background: var(--grey-btn); }

  /* Services */
  .services { position: absolute; left: 0; top: 1021px; width: 1200px; height: 519px; background: linear-gradient(180deg, var(--panel) 0%, var(--panel) 43%, #e9e9e9 44%, #f6f6f6 72%, var(--white) 73%); }
  .services h2 { position: absolute; left: 0; top: 50px; width: 1200px; text-align: center; font-size: 28px; color: var(--ink); }
  .service-card { position: absolute; top: 113px; width: 308px; height: 344px; background: var(--white); border: 1px solid #cfcfcf; box-shadow: 0 1px 3px rgba(0,0,0,0.15); text-align: center; }
  .service-photo { width: 100%; height: 188px; }
  .service-card h3 { font-family: "Lato", Arial, sans-serif; font-weight: 400; font-size: 23px; color: #111; margin-top: 18px; }
  .service-card p { font-size: 13.5px; line-height: 20px; color: #666; margin: 8px 26px 0; }
  .service-card .btn-pill { left: 87px; top: 325px; width: 134px; height: 39px; background: var(--red); }
  .slider-arrow { position: absolute; top: 1296px; }

  /* Why choose us */
  .why { position: absolute; left: 0; top: 1540px; width: 1200px; height: 443px; overflow: hidden; }
  .why-photo { position: absolute; inset: 0; background: linear-gradient(120deg, #4a4641 0%, #6e5a3e 45%, #3a3835 75%, #2c2b2a 100%); }
  .why-shape { position: absolute; left: 0; top: 0; }
  .why h2 { position: absolute; left: 122px; top: 104px; font-size: 29px; color: var(--white); }
  .why p { position: absolute; left: 122px; top: 155px; width: 400px; font-size: 18px; line-height: 30.5px; color: var(--white); }
  .why .btn-pill { left: 117px; top: 297px; width: 151px; height: 40px; background: var(--grey-dark); }

  /* News */
  .news h2 { position: absolute; left: 116px; top: 2043px; font-size: 32px; color: var(--ink-soft); }
  .news-item { position: absolute; top: 2106px; }
  .news-thumb { position: absolute; left: 0; top: 0; width: 178px; height: 178px; border-radius: 50%; border: 1px solid #9a9a9a; padding: 6px; }
  .news-thumb div { width: 100%; height: 100%; border-radius: 50%; }
  .news-body { position: absolute; left: 188px; top: 1px; width: 310px; }
  .news-date { font-size: 14px; color: #555; }
  .news-body h3 { font-family: "Open Sans", Arial, sans-serif; font-weight: 400; font-size: 21px; color: #222; margin-top: 5px; }
  .news-body p { font-size: 12px; line-height: 18px; color: #666; margin-top: 7px; }
  .news-more { display: block; margin-top: 12px; font-family: "Lato", Arial, sans-serif; font-weight: 700; font-size: 13px; color: var(--red); text-transform: uppercase; }

  /* Footer */
  .site-footer { position: absolute; left: 0; top: 2350px; width: 1200px; height: 276px; background: var(--grey-mid); color: var(--white); }
  .footer-col { position: absolute; top: 50px; }
  .footer-col h4 { font-family: "Lato", Arial, sans-serif; font-weight: 400; font-size: 20px; text-transform: uppercase; }
  .footer-col ul { list-style: none; margin-top: 20px; }
  .footer-col li { font-size: 14px; line-height: 31px; margin-left: 3px; }
  .contact-list li { display: flex; align-items: center; gap: 14px; margin-left: 0; }
  .contact-list li.cont { padding-left: 30px; }
  .social { display: flex; gap: 7px; margin-top: 20px; }
  .social span { width: 37px; height: 37px; border-radius: 50%; border: 2px solid var(--white); }
  .copyright { position: absolute; left: 0; top: 2626px; width: 1200px; height: 61px; background: var(--grey-dark); color: #aaaaaa; font-size: 13px; display: flex; align-items: center; justify-content: center; }
</style>
</head>
<body>

<header class="site-header">
  <div class="brand">
    <div class="brand-dot"></div>
    <div class="brand-name">Brackenford<br>Fluidworks</div>
  </div>
  <div class="pickup-note">
    <svg width="22" height="16" viewBox="0 0 22 16"><path fill="#ec1f27" d="M0 1h13v10H0zM14 4h4l4 4v3h-8zM2 12h18v1H2z"/><circle cx="5" cy="13.5" r="2.3" fill="#ec1f27"/><circle cx="17" cy="13.5" r="2.3" fill="#ec1f27"/></svg>
    Free pick up and delivery upto 100 miles
  </div>
  <nav class="main-nav">
    <span class="active">Home</span><span>About Us</span><span>Services</span><span>Blogs</span><span>Why Us</span><span>Contact</span>
  </nav>
</header>

<section class="hero">
  <div class="abs" style="inset:0" role="img" aria-label="Flatbed equipment trailer with hydraulic cylinders chained to its deck"></div>
  <h1 class="hero-title heading">30 Years Experience in the<br>Hydraulic Business</h1>
  <div class="btn-outline">Read More</div>
  <div class="slider-dots"><span class="current"></span><span></span><span></span><span></span></div>
</section>

<section class="about" role="region" aria-label="About our company">
  <div class="abs" style="inset:0" role="img" aria-label="Red-tinted photo of hydraulic cylinders in the workshop"></div>
  <h2 class="heading">About Our Company</h2>
  <p>Brackenford Fluidworks is a full hydraulic repair facility. We have 2 shops. We repair and service all hydraulic cylinders, pneumatic cylinders, hydraulic pumps, motors, valves and gearboxes. Our services range from large industrial plants to the individual that owns one piece of equipment. We also offer removal and install of cylinders. Along with free pick up and delivery, within a certain distance which is usually 100 miles from one of our shops.</p>
  <div class="btn-pill">Read More</div>
</section>

<section class="services">
  <h2 class="heading">Services Provide</h2>

  <article class="service-card" style="left:116px">
    <div class="service-photo" role="img" aria-label="Long hydraulic cylinders laid out on the shop floor" style="background:linear-gradient(135deg,#7a6f63,#a25a4a 50%,#5e5650)"></div>
    <h3>Repair Hydraulic Cylinders</h3>
    <p>Morbi diam mauris viverra in gravida eu mattis in ante Morbi eget arcu Morbi porta libero id ullamcorper</p>
    <div class="btn-pill">Read More</div>
  </article>

  <article class="service-card" style="left:441px">
    <div class="service-photo" role="img" aria-label="Yellow pneumatic cylinders resting on a wooden pallet" style="background:linear-gradient(135deg,#8a7a5e,#c9b04a 50%,#7d6f56)"></div>
    <h3>Repair Pneumatic Cylinders</h3>
    <p>Morbi diam mauris viverra in gravida eu mattis in ante Morbi eget arcu Morbi porta ullamcorper</p>
    <div class="btn-pill">Read More</div>
  </article>

  <article class="service-card" style="left:770px">
    <div class="service-photo" role="img" aria-label="Cylinder being removed from equipment in the workshop" style="background:linear-gradient(135deg,#8c8a86,#c9c3b8 50%,#6f6b66)"></div>
    <h3>Removal &amp; Install</h3>
    <p>Morbi diam mauris viverra in gravida eu mattis in ante Morbi eget arcu Morbi porta libero id ullamcorper</p>
    <div class="btn-pill">Read More</div>
  </article>

  <svg class="slider-arrow" style="left:80px;top:275px" width="20" height="36" viewBox="0 0 20 36"><path d="M17 2 3 18l14 16" fill="none" stroke="#9a9a9a" stroke-width="3"/></svg>
  <svg class="slider-arrow" style="left:1096px;top:275px" width="20" height="36" viewBox="0 0 20 36"><path d="M3 2l14 16L3 34" fill="none" stroke="#9a9a9a" stroke-width="3"/></svg>
</section>

<section class="why">
  <div class="why-photo" role="img" aria-label="Hydraulic cylinder and blue pump strapped to a pallet in a truck bed"></div>
  <svg class="why-shape" width="600" height="443" viewBox="0 0 600 443"><polygon points="0,0 600,0 385,443 0,443" fill="#ec1f27"/></svg>
  <h2 class="heading">Why Choose Us</h2>
  <p>With over 30 years experience in the hydraulic business, we can repair or replace any job. There is not a job too big or too small, we service them all</p>
  <div class="btn-pill">Read More</div>
</section>

<section class="news">
  <h2 class="heading">Latest News</h2>

  <article class="news-item" style="left:100px">
    <div class="news-thumb"><div role="img" aria-label="Close-up of a repaired cylinder rod" style="background:radial-gradient(circle at 50% 45%,#a9a9a5,#4a4a48)"></div></div>
    <div class="news-body">
      <div class="news-date">05 JAN 2018</div>
      <h3>Your News Title here</h3>
      <p>Rebuilt a pair of loader lift cylinders with new seals, honed barrels and chrome rods, then returned them pressure tested within the week.</p>
      <span class="news-more">Read More</span>
    </div>
  </article>

  <article class="news-item" style="left:595px">
    <div class="news-thumb"><div role="img" aria-label="Yellow hydraulic cylinder ready for delivery" style="background:radial-gradient(circle at 50% 45%,#e0c23a,#6b6556)"></div></div>
    <div class="news-body">
      <div class="news-date">05 JAN 2018</div>
      <h3>Your News Title here</h3>
      <p>A boom truck came in for a full hydraulic overhaul covering pump, valves and swing motor, finished and delivered back to the jobsite on time.</p>
      <span class="news-more">Read More</span>
    </div>
  </article>
</section>

<footer class="site-footer">
  <div class="footer-col" style="left:116px">
    <h4>Quick Links</h4>
    <ul><li>Home</li><li>About Us</li><li>Our Services</li><li>Why Us</li></ul>
  </div>
  <div class="footer-col" style="left:353px">
    <h4>Resources</h4>
    <ul><li>Career</li><li>Team</li><li>Testimonials</li><li>Contact Us</li></ul>
  </div>
  <div class="footer-col" style="left:582px">
    <h4>Contact Us</h4>
    <ul class="contact-list">
      <li><svg width="16" height="20" viewBox="0 0 16 20"><path d="M8 1a6 6 0 0 0-6 6c0 4.5 6 12 6 12s6-7.5 6-12a6 6 0 0 0-6-6z" fill="#fff"/><circle cx="8" cy="7" r="2.2" fill="#9a9a9a"/></svg>42 Millrace Road #B</li>
      <li class="cont">Texas 75990 TX</li>
      <li><svg width="16" height="18" viewBox="0 0 16 18"><path d="M3 1l3 3-2 3c1 2.5 3 4.5 5.5 5.5l2.5-2 3 3-2 3C7 16 1 9 1 3z" fill="none" stroke="#fff" stroke-width="1.3"/></svg>555.014.2290</li>
      <li><svg width="16" height="12" viewBox="0 0 16 12"><rect x="0.7" y="0.7" width="14.6" height="10.6" fill="none" stroke="#fff" stroke-width="1.3"/><path d="M1 1l7 6 7-6" fill="none" stroke="#fff" stroke-width="1.3"/></svg>info@brackenford.example</li>
    </ul>
  </div>
  <div class="footer-col" style="left:874px">
    <h4>Follow Us</h4>
    <div class="social"><span></span><span></span><span></span><span></span></div>
  </div>
</footer>

<div class="copyright">© 2018 Brackenford Fluidworks &nbsp;All right reserved</div>

</body>
</html>
```